Thoroughbred Racing Partnership needs web design

Glimmer of Laurel Partners is a management group who buys horses and races them on both the West and East coasts. The premise of the business is for an investment as little as $500, anyone can be a partner and own a percentage of a horse(s). This is a low cost way of getting involved in the exciting sport of Thoroughbred Racing, without shouldering the heavy financial responsibility. Our target market is mostly males 40+ but we want to include all target markets. We are looking for something very clean and professional, we want to give an image of success. Nothing overly "artsy." I have included the logo in which you can incorporate in the site. Also, the logo colors will be the colors of our "silks." The silks are what the jockey wears and will be an important marketing tool for GOL. We would like a very prominent picture of a racehorse somewhere on the homepage, we want to make it clear that is a website for Horseracing partnerships.

On the top of the site, it should say "Glimmer of Laurel" (on the top)
and below that "Thoroughbred Racing Partnerships." (below that)

The main sections, which should be across the top are:

Home
About Us
Ownership
Stable Roster
News
Contact us

Some of these will have drop down menus.

An example of a competitor website that we like is: www.harrowgatefarm.example
An example of a competitor website that we don't like is: www.paddockvue.example
Updates

Project Deadline Extended
Reason: We have a Board of Directors meeting on the 22nd and we will be making a decision on that day. I'm giving an extension so that all designers are able to submit their designs by the 22nd. Thank you!

Target Market(s)

40+ males

Industry/Entity Type

Business

Requirements
Must have
• our logo must be on the site. We would like at least one bold image of a thoroughbred horse in action. The picture is going to tell the story so it needs to be very eye-catching.

Our slogan should also be included on the website, "Experience the thrill of owning a Racehorse."
Should not have
• cartoons, artsy pictures, pictures of Steeplechase horses or "jumpers." This partnership is for racehorses only, there is not jumping involved with the horses.

```html
<!DOCTYPE html>
<html lang="en">
<head>
<meta charset="utf-8">
<title>Glimmer of Laurel Partners – Thoroughbred Racing Partnerships</title>
<link rel="stylesheet" href="https://fonts.googleapis.com/css2?family=Oswald:wght@400;500&family=Open+Sans:ital,wght@0,400;0,600;0,700;1,400&display=swap">
<style>
:root{
  --blue:#135a8b;
  --blue-mid:#1a6aa0;
  --navy:#0b1c4f;
  --nav-dark:#0c2b4a;
  --footer:#0b1724;
  --footer-line:#1d3347;
  --link:#1a5f95;
  --accent:#3a9ad9;
  --grey:#e6e6e6;
  --card:#f2f2f2;
  --white:#ffffff;
  --text:#444;
  --hero-a:#5b7a3a;
  --hero-b:#2f4a1f;
}
*{box-sizing:border-box;margin:0;padding:0}
html,body{width:1059px;height:1200px;overflow:hidden}
body{position:relative;font-family:"Open Sans",sans-serif;background:var(--grey);color:var(--text)}
.abs{position:absolute}

/* header */
.header{left:0;top:0;width:1059px;height:74px;background:var(--blue)}
.tagline{left:687px;top:8px;color:#e4eef7;font-style:italic;font-size:14.5px;line-height:22px}
.nav{left:124px;top:58px;width:811px;height:49px;background:var(--nav-dark);border:1px solid #1e4d78;border-radius:7px;z-index:2}
.nav ul{list-style:none;position:absolute;left:274px;top:11px;display:flex;align-items:center}
.nav li{font-weight:700;font-size:11.8px;color:var(--white);padding:0 14px;border-left:1px solid #2a5680;line-height:20px}
.nav li:first-child{border-left:none;padding:0}
.nav li.active{background:linear-gradient(#f3f7fb,#b9cbdc);color:var(--navy);border-radius:3px;padding:2px 8px;margin-right:6px}
.logo{left:136px;top:7px;width:206px;height:99px;background:#f4f7fa;z-index:3;display:flex;align-items:center;justify-content:center;flex-direction:column}
.logo-name{font-family:"Open Sans",sans-serif;font-weight:700;color:var(--navy);font-size:34px;line-height:36px;letter-spacing:2px}
.logo-sub{font-family:"Open Sans",sans-serif;font-weight:700;color:var(--navy);font-size:15px;line-height:20px}

/* hero */
.hero{left:0;top:74px;width:1059px;height:486px;background:linear-gradient(180deg,#3c5a2c 0%,#6f8f4a 45%,#c9d4c2 62%,#7d9b4e 75%,#5f7f36 100%)}
.slogan{left:136px;top:188px;font-family:"Oswald",sans-serif;font-size:45px;line-height:52px;color:var(--white);font-weight:400}
.dots{left:815px;top:531px;display:flex;gap:4px}
.dots span{width:31px;height:7px;background:var(--navy)}
.dots span.on{background:var(--white)}

/* about */
.about{left:0;top:560px;width:1059px;height:194px;background:var(--blue)}
.about-title{left:126px;top:570px;font-family:"Oswald",sans-serif;font-size:23px;color:var(--white);display:flex;align-items:baseline;gap:12px}
.about-title b{font-family:"Open Sans",sans-serif;font-weight:700;font-size:23px;color:var(--navy)}
.about-rule{left:126px;top:606px;width:527px;height:1px;background:#4f85ad}
.about-text{left:126px;top:620px;width:537px;color:var(--white);font-weight:700;font-size:11.6px;line-height:18.5px}
.btn{display:flex;align-items:center;justify-content:center;font-family:Arial,sans-serif;font-weight:700;font-size:10.5px;border-radius:3px}
.btn-light{background:linear-gradient(#fff,#dde7f0);color:var(--link)}
.btn-dark{background:var(--blue);color:var(--white)}
.video{left:683px;top:571px;width:250px;height:171px;border:1px solid #fff;background:#111}
.video-shot{position:absolute;left:0;top:0;width:248px;height:145px;background:linear-gradient(135deg,#2a2a2a,#5b4a3e 50%,#1c1c1c)}
.video-bar{position:absolute;left:0;bottom:0;width:248px;height:24px;background:linear-gradient(#3a3a3a,#1a1a1a);color:#ccc;font-size:8px}

/* cards */
.card{width:265px;height:246px;top:777px;background:linear-gradient(#f7f7f5,#d4d4d4);border-radius:0 0 6px 6px;box-shadow:0 2px 3px rgba(0,0,0,.25)}
.card-head{position:absolute;left:0;top:0;width:265px;height:33px;background:var(--navy)}
.card-icon{position:absolute;left:5px;top:-3px;width:39px;height:39px;border-radius:50%;background:var(--white)}
.card-title{position:absolute;left:64px;top:0;font-family:"Oswald",sans-serif;color:var(--white);font-size:22px;line-height:33px}
.card-text{position:absolute;left:9px;top:44px;width:250px;font-size:10.4px;line-height:16.3px;color:#555}
.ticks{position:absolute;left:10px;top:136px;list-style:none}
.ticks li{font-weight:700;font-size:10.4px;color:var(--link);line-height:18.5px;padding-left:23px;position:relative}
.ticks svg{position:absolute;left:0;top:4px}
.news-item{position:absolute;left:15px;display:flex}
.news-date{width:36px;text-align:center;font-size:14px;line-height:14px;color:var(--link);border-right:1px solid #888;padding-right:6px;margin-right:12px}
.news-body{font-size:10.4px;line-height:14px;color:#555;width:180px}
.news-body b{color:var(--link);font-weight:600}
.field{position:absolute;left:9px;width:239px;height:22px;background:#fafaf8;border:1px solid #c9c9c9;font-size:10px;color:#555;padding:4px 9px}

/* footer */
.footer{left:0;top:1046px;width:1059px;height:154px;background:var(--footer)}
.fdiv{top:1052px;width:1px;height:140px;background:var(--footer-line)}
.fhead{font-size:13.5px;font-weight:600;color:var(--accent);border-bottom:1px dashed #4a5e70;padding-bottom:1px;width:100%}
.fcol{top:1060px}
.fcol ul{list-style:none;margin:8px 0 0 9px}
.fcol li{font-size:10.4px;line-height:15px;color:#e5e9ee}
.fcol li:first-child{color:var(--accent)}
.ftext{font-size:10.4px;line-height:15px;color:#e5e9ee}
.finput{width:147px;height:22px;border:1px solid #24476a;background:#0f2c46;font-style:italic;font-size:9px;color:#8fa7bd;padding:4px 6px}
.fline{display:flex;align-items:center;gap:7px;font-weight:700;font-size:10.4px;color:var(--white)}
.social{left:788px;top:1133px;display:flex;gap:10px}
.social span{width:24px;height:24px;border-radius:50%;background:#17528a;border:1px solid #2f6ea6}
</style>
</head>
<body>

<div class="abs header"></div>
<p class="abs tagline">Glimmer of Laurel<br>Thoroughbred Racing Partnerships.</p>

<div class="abs logo">
  <span class="logo-name">GOL</span>
  <span class="logo-sub">PARTNERS.EXAMPLE</span>
</div>

<nav class="abs nav">
  <ul>
    <li class="active">HOME</li>
    <li>ABOUT US</li>
    <li>OWNERSHIP</li>
    <li>STABLE ROSTER</li>
    <li>NEWS</li>
    <li>CONTACT US</li>
  </ul>
</nav>

<div class="abs hero" role="img" aria-label="Photo of a jockey in red, white and blue silks riding a dark bay thoroughbred at full gallop on a grass track with white rails"></div>
<h1 class="abs slogan">Experience the thrill of<br>owning a Racehorse</h1>
<div class="abs dots"><span class="on"></span><span></span><span></span></div>

<section class="abs about"></section>
<h2 class="abs about-title">About Company <b>GOL</b></h2>
<div class="abs about-rule"></div>
<p class="abs about-text">Glimmer of Laurel Partners is a management group who buys horses and races them on both the West and East coasts. The premise of the business is for an investment as little as $500, anyone can be a partner and own a percentage of a horse(s). This is a low cost way of getting involved in the exciting sport of Thoroughbred Racing, without shouldering the heavy financial responsibility.</p>
<a class="abs btn btn-light" style="left:566px;top:711px;width:79px;height:20px">Read more »</a>

<div class="abs video">
  <div class="video-shot" role="img" aria-label="Video still of three partners presenting a racing award plaque"></div>
  <svg style="position:absolute;left:102px;top:55px" width="40" height="40" viewBox="0 0 40 40"><rect width="40" height="40" rx="4" fill="#c0272d"/><path d="M14 10 L30 20 L14 30Z" fill="#fff"/></svg>
  <div class="video-bar">
    <svg style="position:absolute;left:18px;top:7px" width="10" height="11"><rect width="3" height="11" fill="#ccc"/><rect x="6" width="3" height="11" fill="#ccc"/></svg>
    <svg style="position:absolute;left:54px;top:7px" width="16" height="11"><path d="M0 3h4l5-3v11l-5-3H0z" fill="#ccc"/><path d="M11 2q3 3.5 0 7" stroke="#ccc" fill="none"/></svg>
    <span style="position:absolute;left:82px;top:6px">0:00 / 0:00</span>
  </div>
</div>

<!-- why choose -->
<div class="abs card" style="left:124px">
  <div class="card-head"><div class="card-icon"></div><h3 class="card-title">Why Choose GOL</h3></div>
  <p class="card-text">Lorem ipsum dolor sit amet, consectet adipiscing elit, sed diam nonummy nibh euismod tincidunt ut laoreet dolore magna aliquam erat volutpat.Ut wisi enim ad minim veniam, quis nostru exe ullamcorper suscipit lobortis nisl ut aliquip commod consequat.</p>
  <ul class="ticks">
    <li><svg width="14" height="11"><path d="M1 6l4 4 8-9" stroke="#1a6aa0" stroke-width="1.6" fill="none"/></svg>Lorem ipsum dolor sit amet</li>
    <li><svg width="14" height="11"><path d="M1 6l4 4 8-9" stroke="#1a6aa0" stroke-width="1.6" fill="none"/></svg>Sed diam nonummy nibh euismod</li>
    <li><svg width="14" height="11"><path d="M1 6l4 4 8-9" stroke="#1a6aa0" stroke-width="1.6" fill="none"/></svg>Ut wisi enim ad minim</li>
    <li><svg width="14" height="11"><path d="M1 6l4 4 8-9" stroke="#1a6aa0" stroke-width="1.6" fill="none"/></svg>Consectet adipiscing elit</li>
  </ul>
  <a class="abs btn btn-dark" style="left:169px;top:216px;width:79px;height:20px">Read more »</a>
</div>

<!-- news -->
<div class="abs card" style="left:397px">
  <div class="card-head"><div class="card-icon">
    <svg style="position:absolute;left:9px;top:11px" width="22" height="18" viewBox="0 0 22 18"><path d="M2 6h4l12-5v16L6 12H2z" fill="#1a5f95"/><rect x="5" y="12" width="3" height="5" fill="#1a5f95"/></svg>
  </div><h3 class="card-title">GOL News</h3></div>
  <div class="news-item" style="top:50px"><div class="news-date">20<br>Oct</div><p class="news-body"><b>Lorem ipsum dolor sit amet</b><br>consectetuer adipsi seddiam nonum nibh euismod tincidunt utopi laoree</p></div>
  <div class="news-item" style="top:100px"><div class="news-date">14<br>Oct</div><p class="news-body"><b>Lorem ipsum dolor sit amet</b><br>consectetuer adipsi seddiam nonum nibh euismod tincidunt utopi laoree</p></div>
  <div class="news-item" style="top:149px"><div class="news-date">03<br>Oct</div><p class="news-body"><b>Lorem ipsum dolor sit amet</b><br>consectetuer adipsi seddiam nonum nibh euismod tincidunt utopi laoree</p></div>
  <a class="abs btn btn-dark" style="left:160px;top:216px;width:88px;height:20px">View all news »</a>
</div>

<!-- contact -->
<div class="abs card" style="left:670px">
  <div class="card-head"><div class="card-icon">
    <svg style="position:absolute;left:12px;top:9px" width="16" height="20" viewBox="0 0 16 20"><rect x="1" y="1" width="14" height="18" fill="none" stroke="#1a5f95" stroke-width="2"/><path d="M4 14l7-7" stroke="#1a5f95" stroke-width="2"/></svg>
  </div><h3 class="card-title">Quick Contact</h3></div>
  <div class="field" style="top:50px">Your Name</div>
  <div class="field" style="top:78px">Email</div>
  <div class="field" style="top:107px">Phone</div>
  <div class="field" style="top:137px;height:62px">Message</div>
  <a class="abs btn btn-dark" style="left:169px;top:216px;width:79px;height:20px">Submit</a>
</div>

<!-- footer -->
<footer class="abs footer"></footer>
<div class="abs fdiv" style="left:265px"></div>
<div class="abs fdiv" style="left:505px"></div>
<div class="abs fdiv" style="left:746px"></div>

<div class="abs fcol" style="left:126px;width:99px">
  <h4 class="fhead">Quick Links</h4>
  <ul><li>Home</li><li>About Us</li><li>Ownership</li><li>Stable Roster</li><li>News</li><li>Contact us</li></ul>
</div>

<div class="abs fcol" style="left:301px;width:166px">
  <h4 class="fhead">Newsletter Signup</h4>
  <p class="ftext" style="margin:7px 0 0 3px;line-height:12px">Signup with us and get news and<br>update in your inbox</p>
  <div class="finput" style="margin-top:12px">Email here</div>
  <a class="btn btn-light" style="margin:7px 0 0 75px;width:72px;height:21px;font-family:'Open Sans',sans-serif;font-size:11.5px;color:var(--navy)">Signup</a>
</div>

<div class="abs fcol" style="left:543px;width:166px">
  <h4 class="fhead">Company Headquarter</h4>
  <p class="ftext" style="margin:6px 0 0 3px;line-height:16.5px">Lorem ipsum dolor sit amet<br>consectetuer adipsi<br>Po Box-0050</p>
  <div class="fline" style="margin:4px 0 0 2px"><svg width="12" height="12" viewBox="0 0 12 12"><path d="M2 1l2 0 1 3-1.5 1q1 2.5 3.5 3.5l1-1.5 3 1v2q-1 1.5-3 1Q2 9 1 3q0-1.5 1-2z" fill="#c8d8e8"/></svg>001 555-0142</div>
  <div class="fline" style="margin:8px 0 0 2px"><svg width="14" height="10"><rect width="14" height="10" fill="#c8d8e8"/><path d="M0 0l7 6 7-6" stroke="#0b1724" fill="none"/></svg>info@golpartners.example</div>
</div>

<div class="abs" style="left:792px;top:1066px;width:118px;text-align:center;color:#e5e9ee">
  <div style="font-weight:700;font-size:30px;line-height:32px;letter-spacing:2px">GOL</div>
  <div style="font-weight:700;font-size:13px;line-height:18px">PARTNERS.EXAMPLE</div>
</div>
<div class="abs social"><span></span><span></span><span></span><span></span></div>
<p class="abs" style="left:786px;top:1168px;font-size:8.3px;color:#e5e9ee">© 2013 Glimmer of Laurel Partners</p>

</body>
</html>
```